Stonebrace Business Card Design

The Stonebrace Co is an aggregate (crushing) equipment dealer serving Western Canadian provinces. Stonebrace is a distributor of aggregate equipment for different manufacturers.

We are looking to change and update the existing business card which has been used since the existence of the company. A copy of existing card has been attached for reference. The Stonebrace Co logo we want to remain the same and we want the green color to remain the same.

We are wanting something new with a different look. A refreshing card to show a new modern and updated look. No longer wanting to have the manufacturers on the back of the card but something more like our logo on the back of the card with a statement like "Crushing Solutions"

ideas could be:
- card can be different colors on front and back
- front or reverse of the card could possibly be the green color with the logo in black

Target Market(s)

Owners of Aggregate/Crushing companies

Contact Information for Business Card

see above

Requirements
Must have
• - logo to remain same along with same font within logo
• - green color to remain same
Nice to have
• as noted above under project description
Should not have

```html
<!DOCTYPE html>
<html lang="en">
<head>
<meta charset="utf-8">
<title>The Stonebrace Co — Business Card</title>
<link rel="stylesheet" href="https://fonts.googleapis.com/css2?family=Roboto:wght@400;500;700&family=Roboto+Condensed:wght@700&display=swap">
<style>
  :root {
    --backdrop: #5b4737;
    --charcoal: #231f20;
    --olive: #8a8c08;
    --olive-deep: #7a7c06;
    --white: #ffffff;
    --card-shadow: 0 3px 5px rgba(0,0,0,0.45);
  }
  * { box-sizing: border-box; margin: 0; padding: 0; }
  html, body {
    width: 1200px; height: 960px; overflow: hidden;
    background: var(--backdrop);
    font-family: "Roboto", Arial, sans-serif;
  }
  .stage { position: relative; width: 1200px; height: 960px; }

  .card {
    position: absolute;
    width: 600px; height: 343px;
    border-radius: 20px;
    overflow: hidden;
    box-shadow: var(--card-shadow);
  }

  /* Front */
  .card-front { left: 314px; top: 113px; background: var(--charcoal); }
  .front-art {
    position: absolute; top: 0; right: 0; bottom: 0;
    width: 118px;
    border-top-left-radius: 60px 172px;
    border-bottom-left-radius: 60px 172px;
    background: linear-gradient(160deg, var(--olive) 0%, var(--olive-deep) 100%);
  }
  .contact {
    position: absolute; left: 29px; top: 77px;
    color: var(--white);
  }
  .contact-name {
    font-family: "Roboto Condensed", "Arial Narrow", sans-serif;
    font-weight: 700; font-size: 21px; line-height: 1;
    color: var(--olive);
  }
  .contact-title { font-size: 15px; font-weight: 500; margin-top: 3px; }
  .contact-address { font-size: 14.5px; line-height: 17.5px; margin-top: 16px; }
  .contact-lines { list-style: none; margin-top: 15px; font-size: 14.5px; line-height: 19px; }
  .contact-lines li { display: flex; align-items: center; gap: 8px; }
  .contact-lines svg { width: 15px; height: 14px; flex: none; fill: var(--olive); }

  .front-brand { position: absolute; left: 222px; top: 147px; color: var(--white); }
  .front-brand-name { font-weight: 700; font-size: 20px; letter-spacing: 1.4px; }
  .front-brand-web { font-size: 14px; letter-spacing: 5.2px; margin-top: 2px; padding-left: 11px; }

  /* Back */
  .card-back { left: 311px; top: 472px; background: var(--olive); }
  .back-brand {
    position: absolute; left: 136px; top: 150px;
    display: flex; align-items: center; gap: 67px;
  }
  .back-brand-dot { width: 44px; height: 44px; border-radius: 50%; background: var(--charcoal); }
  .back-brand-name { font-weight: 700; font-size: 22px; letter-spacing: 1.9px; color: var(--charcoal); }
  .back-tagline {
    position: absolute; left: 18px; right: 0; top: 291px;
    text-align: center; font-weight: 500; font-size: 15px; color: var(--charcoal);
  }
</style>
</head>
<body>
<main class="stage">

  <section class="card card-front" aria-label="Card front">
    <div class="front-art" role="img" aria-label="Green flowing wave decoration"></div>

    <div class="contact">
      <p class="contact-name">DALE MARSTEN</p>
      <p class="contact-title">CEO/FOUNDER</p>
      <p class="contact-address">2210- 48B Avenue<br>Leduc, Alberta T9E 3K7</p>
      <ul class="contact-lines">
        <li><svg viewBox="0 0 16 16" aria-label="Phone"><path d="M3.5 1 L6 1 L7 4.5 L5.3 6 C6.2 8 8 9.8 10 10.7 L11.5 9 L15 10 L15 12.5 C15 14 14 15 12.5 15 C6.5 15 1 9.5 1 3.5 C1 2 2 1 3.5 1 Z"/></svg>780.555.0142</li>
        <li><svg viewBox="0 0 16 16" aria-label="Mobile"><path d="M4.5 0.5 H11.5 V15.5 H4.5 Z M6 2.5 V12 H10 V2.5 Z M7.3 13 H8.7 V14.3 H7.3 Z"/></svg>780.555.0187</li>
        <li><svg viewBox="0 0 16 16" aria-label="Fax"><path d="M4 1 H12 V5 H4 Z M1 6 H15 V12 H12.5 V10 H3.5 V12 H1 Z M4.5 11 H11.5 V15 H4.5 Z"/></svg>780.555.0163</li>
        <li><svg viewBox="0 0 16 16" aria-label="Email"><path d="M1 3.5 H15 V12.5 H1 Z M2.2 4.5 L8 9 L13.8 4.5 Z"/></svg>dale@stonebr.com</li>
      </ul>
    </div>

    <div class="front-brand">
      <p class="front-brand-name">THE STONEBRACE CO.</p>
      <p class="front-brand-web">www.stonebrace.ca</p>
    </div>
  </section>

  <section class="card card-back" aria-label="Card back">
    <div class="back-brand">
      <span class="back-brand-dot" aria-hidden="true"></span>
      <span class="back-brand-name">THE STONEBRACE CO.</span>
    </div>
    <p class="back-tagline">Crushing Solutions</p>
  </section>

</main>
</body>
</html>
```